Doctor business card, bold, modern, stand out, keep worthy

I'm a specialist doctor (Oncology and hematology) and I need a flashy business card to hand out to other doctors. I am looking for something that stands out, either with embossing or transparency or high quality paper. I want my card not to look or feel generic. I'm a hematology oncology specialist, and somewhere on the card I should incorporate the TLVB logo, along with my name, my title (hematology/oncology) and board certifications (in oncology and internal medicine), finally with our practice address (82 Orchard Ave Suite 4 Edison NJ 08815) and tel and fax numbers

Target Market(s)

other doctors, patients

Industry/Entity Type

Healthcare

Contact Information for Business Card

1. my name 2. Job title (hematology/Oncology) 3. credentials (Board Certified Medical Oncology/Board Certified Internal Medicine) 4. Address 5. Phone and Fax Number

Font styles to use
Serif

Colors

Designer to choose colors to be used in the design.

Requirements
Nice to have
• flip side can have logo and date of appt blank line. Blue green colors but can vary

```html
<!DOCTYPE html>
<html lang="en">
<head>
<meta charset="utf-8">
<title>TLVB Business Card – Marena Holvik</title>
<link href="https://fonts.googleapis.com/css2?family=Open+Sans:wght@400;600;700&display=swap" rel="stylesheet">
<style>
  :root {
    --stage: #242424;
    --card: #1e1e21;
    --card-deep: #141416;
    --cyan: #1fb6de;
    --magenta: #a2439a;
    --white: #f4f4f4;
    --sheen: #6c6c70;
    --leaf-slate: #2b343b;
    --leaf-plum: #352c36;
  }
  * { margin: 0; padding: 0; box-sizing: border-box; }
  html, body { width: 1200px; height: 780px; overflow: hidden; }
  body {
    background: var(--stage);
    font-family: "Open Sans", Arial, sans-serif;
    color: var(--white);
    position: relative;
  }
  .card {
    position: absolute;
    width: 530px;
    height: 303px;
    background: var(--card);
    border-bottom: 6px solid var(--cyan);
    box-shadow: 0 14px 30px rgba(0,0,0,0.55);
    overflow: hidden;
  }
  .card--front { left: 50px; top: 80px; }
  .card--back { left: 620px; top: 395px; }

  /* front */
  .front-pattern {
    position: absolute; inset: 0;
    background: linear-gradient(215deg, var(--sheen) 0%, #3a3a3d 22%, var(--card-deep) 48%, var(--card) 100%);
  }
  .brand {
    position: absolute; left: 30px; top: 26px;
    display: flex; align-items: center; gap: 8px;
  }
  .brand-dot { width: 14px; height: 14px; border-radius: 50%; background: var(--magenta); }
  .brand-name {
    font-size: 30px; font-weight: 400; letter-spacing: 4px; color: var(--cyan);
  }
  .credentials {
    position: absolute; right: 24px; bottom: 18px;
    font-size: 14.5px; font-weight: 600; letter-spacing: 0.3px; color: var(--white);
  }

  /* back */
  .back-leaf {
    position: absolute; left: 150px; top: 20px; width: 300px; height: 270px;
    background: radial-gradient(ellipse at 45% 55%, var(--leaf-slate) 0%, var(--leaf-plum) 40%, rgba(30,30,33,0) 72%);
    opacity: 0.9;
  }
  .identity {
    position: absolute; left: 62px; top: 96px; text-align: right; width: 190px;
  }
  .doctor-name { font-size: 25px; font-weight: 700; line-height: 1.1; white-space: nowrap; }
  .doctor-name .first { color: var(--cyan); }
  .doctor-name .last { color: var(--magenta); }
  .doctor-title { font-size: 15px; font-weight: 600; margin-top: 2px; }
  .divider {
    position: absolute; left: 268px; top: 78px; width: 2px; height: 92px; background: var(--white);
  }
  .contact-list {
    position: absolute; left: 284px; top: 78px; list-style: none;
    font-size: 13px; line-height: 23px;
  }
  .contact-list li { display: flex; align-items: center; gap: 8px; white-space: nowrap; }
  .contact-list svg { width: 14px; height: 14px; fill: var(--cyan); flex: none; }
  .address {
    position: absolute; left: 0; right: 0; bottom: 26px; text-align: center;
    font-size: 15px; font-weight: 400;
  }
</style>
</head>
<body>
  <section class="card card--front" aria-label="Card front">
    <div class="front-pattern" role="img" aria-label="Glossy repeating leaf pattern across the card, fading from silver at the top right to black"></div>
    <div class="brand">
      <span class="brand-dot"></span>
      <span class="brand-name">TLVB</span>
    </div>
    <p class="credentials">Board Certified Medical Oncology/Board Certified Internal Medicine</p>
  </section>

  <section class="card card--back" aria-label="Card back">
    <div class="back-leaf" role="img" aria-label="Faint large leaf decoration in slate and plum tones"></div>
    <div class="identity">
      <p class="doctor-name"><span class="first">Marena</span> <span class="last">Holvik</span></p>
      <p class="doctor-title">Hematology/Oncology</p>
    </div>
    <div class="divider"></div>
    <ul class="contact-list">
      <li><svg viewBox="0 0 24 24"><path d="M6.6 10.8a15.1 15.1 0 0 0 6.6 6.6l2.2-2.2c.3-.3.7-.4 1-.2 1.1.4 2.3.6 3.6.6.6 0 1 .4 1 1V20c0 .6-.4 1-1 1A17 17 0 0 1 3 4c0-.6.4-1 1-1h3.5c.6 0 1 .4 1 1 0 1.3.2 2.5.6 3.6.1.3 0 .7-.2 1z"/></svg>(844) 555-0172</li>
      <li><svg viewBox="0 0 24 24"><path d="M7 2h10v6H7zM4 9h16a2 2 0 0 1 2 2v9H2v-9a2 2 0 0 1 2-2zm2 4v2h4v-2zm8 0v2h2v-2zm0 3v2h2v-2z"/></svg>(844) 555-0172</li>
      <li><svg viewBox="0 0 24 24"><path d="M12 2a10 10 0 1 0 0 20 10 10 0 0 0 0-20zm-1 17.9A8 8 0 0 1 4 12l5 5v1a2 2 0 0 0 2 2zm6.9-2.5A2 2 0 0 0 16 16h-1v-3a1 1 0 0 0-1-1H8v-2h2a1 1 0 0 0 1-1V7h2a2 2 0 0 0 2-2v-.4a8 8 0 0 1 2.9 12.8z"/></svg>info@orchardcancercare.org</li>
      <li><svg viewBox="0 0 24 24"><path d="M2 5h20v14H2zm2 2v.5l8 5 8-5V7zm0 2.8V17h16V9.8l-8 5z"/></svg>www.orchardcancercare.org</li>
    </ul>
    <p class="address">82 Orchard Ave Suite 4 Edison NJ 08815</p>
  </section>
</body>
</html>
```